Venora Tulesi Parwine

Design a self adhesive label to be placed on a standard 1 pint milk plastic bottle 14.acm x 5.5 cm and 1 litre plastic bottle 17cm X 6.1cm

The product to be packed inside the bottle is a Natural Fermented Milk which looks between Natural Yogurt but with curdle inside.

I have update project to a guaranteed contest

Target Market(s)

Small Ethnic African Community from Southern Africa

Industry/Entity Type

Plastic

Requirements
Must have
• Logo/Brand VENORA and Product Name which is a double word TULESI PARWINE.

```html
<!DOCTYPE html>
<html lang="en">
<head>
<meta charset="utf-8">
<title>Venora Tulesi Parwine – Bottle Label</title>
<link href="https://fonts.googleapis.com/css2?family=Arimo:wght@400;700&display=swap" rel="stylesheet">
<style>
  :root {
    --page: #f2f4f6;
    --sky-top: #1f8fd0;
    --sky-mid: #6cc0ea;
    --sky-low: #d9eef8;
    --cream: #eef1ec;
    --deep-blue: #123a78;
    --name-blue: #1a5db5;
    --white: #ffffff;
    --badge-red: #e3131b;
    --text-dark: #1e2a3a;
    --pint-ink: #2b3f66;
  }
  * { margin: 0; padding: 0; box-sizing: border-box; }
  html, body { width: 788px; height: 1200px; overflow: hidden; }
  body { background: var(--page); position: relative; font-family: "Arimo", Arial, sans-serif; }

  .label {
    position: absolute; left: 0; top: 444px; width: 788px; height: 311px; overflow: hidden;
    background: linear-gradient(180deg, var(--sky-top) 0%, var(--sky-mid) 38%, var(--sky-low) 68%, var(--cream) 100%);
  }
  .splash-photo { position: absolute; left: 200px; top: 0; width: 588px; height: 311px; }

  .brand {
    position: absolute; left: 28px; top: 26px;
    font-weight: 700; font-size: 44px; letter-spacing: 1px;
    color: var(--white); line-height: 1;
  }
  .product-type {
    position: absolute; left: 30px; top: 76px;
    font-size: 20px; color: var(--deep-blue); line-height: 1;
  }
  .nutrition { position: absolute; left: 30px; top: 104px; width: 220px; color: var(--text-dark); font-size: 12.5px; line-height: 15px; }
  .nutrition h2 { font-size: 13px; font-weight: 700; }
  .nutrition .rda { margin-bottom: 14px; }
  .nutrition h3 { font-size: 13px; font-weight: 700; margin-bottom: 2px; }
  .nutrition table { border-collapse: collapse; width: 218px; }
  .nutrition td { padding: 0; line-height: 16px; }
  .nutrition td.value { text-align: right; }

  .product-name {
    position: absolute; left: 262px; top: 66px; width: 400px;
    font-weight: 700; font-size: 84px; line-height: 88px;
    color: var(--name-blue); text-align: center;
  }
  .product-name span { display: block; }

  .badge {
    position: absolute; left: 664px; top: 14px; width: 96px; height: 96px; border-radius: 50%;
    background: var(--badge-red); color: var(--white);
    display: flex; align-items: center; justify-content: center; text-align: center;
    font-size: 11.5px; font-weight: 700; line-height: 13px; padding: 8px;
  }
  .volume {
    position: absolute; right: 22px; bottom: 12px;
    font-size: 32px; color: var(--pint-ink); line-height: 1;
  }
</style>
</head>
<body>
  <section class="label">
    <svg class="splash-photo" role="img" aria-label="Photograph of a white milk splash" viewBox="0 0 588 311">
      <defs>
        <radialGradient id="milkGlow" cx="45%" cy="60%" r="60%">
          <stop offset="0" stop-color="#ffffff" stop-opacity="0.95"/>
          <stop offset="0.55" stop-color="#e6f3fa" stop-opacity="0.6"/>
          <stop offset="1" stop-color="#e6f3fa" stop-opacity="0"/>
        </radialGradient>
        <radialGradient id="milkPour" cx="50%" cy="0%" r="100%">
          <stop offset="0" stop-color="#ffffff" stop-opacity="0.8"/>
          <stop offset="1" stop-color="#ffffff" stop-opacity="0"/>
        </radialGradient>
      </defs>
      <rect width="588" height="311" fill="url(#milkGlow)"/>
      <ellipse cx="395" cy="0" rx="60" ry="170" fill="url(#milkPour)"/>
    </svg>

    <div class="brand">venora</div>
    <div class="product-type">Full Cream Milk Powder</div>

    <div class="nutrition">
      <h2>Nutritional Information</h2>
      <p class="rda">Percentages of daily dietary<br>allowance (RDA) recommended<br>for personsolder than 10 years.</p>
      <h3>Nutritional info per 100ml</h3>
      <table>
        <tr><td>Energy</td><td class="value">262 kJ</td></tr>
        <tr><td>Protein</td><td class="value">3.1 g</td></tr>
        <tr><td>Fat</td><td class="value">3.3 g</td></tr>
        <tr><td>Carbohydrates</td><td class="value">5.1 g</td></tr>
        <tr><td>Calcium</td><td class="value">115 mg</td></tr>
      </table>
    </div>

    <h1 class="product-name"><span>Tulesi</span><span>Parwine</span></h1>

    <div class="badge">All the nutrition of fresh milk. Rich in vitamin A, D3 and Iron.</div>

    <div class="volume">1 pint</div>
  </section>
</body>
</html>
```